7 P's for Healthcare Companies - Textbook Graphic

Can you create a graphic for me for a medical textbook? The goal is to show 7 critical features of a healthcare startup and the audience is physicians with limited business backgrounds.

Please include a picture of young, male emergency physician in the middle of the graphic. Show them evaluating an idea. Can you surround the physician with bold writing for the seven components, and use brief descriptions and simple images or graphics to illustrate the point?

The image should be somewhat formal, but it's OK to be lighthearded.

The seven P's and brief descriptions include the following:
Product: what is their market solution?
(Intellectual) Property: do they have a patent or trademark?
Product Clearance: how will they get RLT approval and NVB clearance?
Payment: how will they make money?
Pilots: have they applied their product in a healthcare setting?
Physician and Patient feedback: Do doctors and patients like their product?
Publication: do they have evidence their product works?

More detail and information is available at this website: https://kovantrel.com/blog/uncategorized/healthcare-framework/

I will need to own this image

```html
<!DOCTYPE html>
<html lang="en">
<head>
<meta charset="utf-8">
<title>7 P's for Healthcare Companies</title>
<link rel="stylesheet" href="https://fonts.googleapis.com/css2?family=Arimo:wght@400&family=Oswald:wght@600&family=Roboto:wght@700&display=swap">
<style>
  :root {
    --backdrop: #cfcfcf;
    --page: #ffffff;
    --header: #474645;
    --ink: #111111;
    --ring: #444444;
    --red: #c21f26;
    --orange: #f37c20;
    --green: #458a3d;
    --cyan: #35c6f1;
    --blue: #2f4fa2;
    --purple: #7e5ca8;
    --pink: #ee69a8;
  }
  html, body {
    margin: 0;
    width: 1200px;
    height: 1200px;
    overflow: hidden;
    background: var(--backdrop);
  }
  .poster {
    display: block;
    width: 856px;
    height: 1200px;
    margin: 0 auto;
  }
  .poster-title { font-family: "Roboto", Arial, sans-serif; font-weight: 700; fill: #fff; }
  .poster-title--big { font-size: 142px; }
  .poster-title--sub { font-size: 76px; }
  .p-heading { font-family: "Oswald", "Arial Narrow", sans-serif; font-weight: 600; font-size: 29px; fill: var(--ink); text-anchor: middle; }
  .p-text { font-family: "Arimo", Arial, sans-serif; font-size: 23.5px; fill: var(--ink); text-anchor: middle; }
  .band { stroke: none; }
  .wedge { fill: var(--page); stroke-width: 2.5; }
  .icon-face { fill: #fff; }
  .icon-shadow { fill: #3a3a3a; opacity: .85; }
</style>
</head>
<body>
<svg class="poster" viewBox="0 0 1195 1677" xmlns="http://www.w3.org/2000/svg">
  <defs>
    <path id="band-shape" d="M -195.2 -438.5 A 480 480 0 0 1 195.2 -438.5 L 172.9 -388.2 A 425 425 0 0 0 -172.9 -388.2 Z"/>
    <path id="wedge-shape" d="M -82.8 -195.1 L -166 -391.2 A 425 425 0 0 1 166 -391.2 L 82.8 -195.1 A 212 212 0 0 0 -82.8 -195.1 Z"/>
    <radialGradient id="physician-fill" cx="50%" cy="45%" r="60%">
      <stop offset="0" stop-color="#eef0f2"/>
      <stop offset="1" stop-color="#d9dcdf"/>
    </radialGradient>
  </defs>

  <!-- page -->
  <rect class="page" x="0" y="0" width="1195" height="1677" fill="var(--page)"/>

  <!-- header -->
  <rect class="header" x="0" y="0" width="1195" height="273" fill="var(--header)"/>
  <text class="poster-title poster-title--big" x="597" y="144" text-anchor="middle">7 P's</text>
  <text class="poster-title poster-title--sub" x="582" y="227" text-anchor="middle">for Healthcare Companies</text>

  <!-- wheel -->
  <g class="wheel" transform="translate(597 952)">
    <g class="segment segment--product" transform="rotate(25.7)">
      <use href="#wedge-shape" class="wedge" stroke="var(--orange)"/>
      <use href="#band-shape" class="band" fill="var(--orange)"/>
    </g>
    <g class="segment segment--property" transform="rotate(77.1)">
      <use href="#wedge-shape" class="wedge" stroke="var(--green)"/>
      <use href="#band-shape" class="band" fill="var(--green)"/>
    </g>
    <g class="segment segment--clearance" transform="rotate(128.6)">
      <use href="#wedge-shape" class="wedge" stroke="var(--cyan)"/>
      <use href="#band-shape" class="band" fill="var(--cyan)"/>
    </g>
    <g class="segment segment--payment" transform="rotate(180)">
      <use href="#wedge-shape" class="wedge" stroke="var(--blue)"/>
      <use href="#band-shape" class="band" fill="var(--blue)"/>
    </g>
    <g class="segment segment--pilots" transform="rotate(231.4)">
      <use href="#wedge-shape" class="wedge" stroke="var(--purple)"/>
      <use href="#band-shape" class="band" fill="var(--purple)"/>
    </g>
    <g class="segment segment--feedback" transform="rotate(282.9)">
      <use href="#wedge-shape" class="wedge" stroke="var(--pink)"/>
      <use href="#band-shape" class="band" fill="var(--pink)"/>
    </g>
    <g class="segment segment--publication" transform="rotate(334.3)">
      <use href="#wedge-shape" class="wedge" stroke="var(--red)"/>
      <use href="#band-shape" class="band" fill="var(--red)"/>
    </g>

    <!-- centre: physician evaluating an idea -->
    <circle r="200" fill="var(--page)" stroke="var(--ring)" stroke-width="9"/>
    <circle r="194" fill="url(#physician-fill)" role="img" aria-label="Illustration of a young male emergency physician in a white coat holding a clipboard and a glowing light bulb idea"/>
  </g>

  <!-- icon badges -->
  <g class="badge badge--product" transform="translate(806 519)">
    <circle r="82" fill="#fff" stroke="var(--orange)" stroke-width="2.5"/>
    <circle r="72" fill="var(--orange)"/>
    <circle class="icon-shadow" r="43" cx="7" cy="7"/>
    <circle class="icon-face" r="43"/>
    <circle r="14" fill="none" stroke="var(--orange)" stroke-width="6"/>
    <path d="M -13 14 Q -22 -2 -14 -16 Q 0 -32 14 -16 Q 22 -2 13 14 Z" fill="none" stroke="var(--orange)" stroke-width="4"/>
    <rect x="-9" y="18" width="18" height="10" rx="3" fill="var(--orange)"/>
  </g>

  <g class="badge badge--property" transform="translate(1066 845)">
    <circle r="82" fill="#fff" stroke="var(--green)" stroke-width="2.5"/>
    <circle r="72" fill="var(--green)"/>
    <circle class="icon-shadow" r="43" cx="7" cy="7"/>
    <circle class="icon-face" r="43"/>
    <path d="M -9 8 L -9 30 L 0 24 L 9 30 L 9 8 Z" fill="var(--green)"/>
    <circle r="20" cy="-6" fill="var(--green)"/>
    <circle r="13" cy="-6" fill="#fff"/>
    <path d="M 5 -11 A 7 7 0 1 0 5 -1" fill="none" stroke="var(--green)" stroke-width="3"/>
  </g>

  <g class="badge badge--clearance" transform="translate(973 1252)">
    <circle r="82" fill="#fff" stroke="var(--cyan)" stroke-width="2.5"/>
    <circle r="72" fill="var(--cyan)"/>
    <circle class="icon-shadow" r="43" cx="7" cy="7"/>
    <circle class="icon-face" r="43"/>
    <path d="M -10 -26 L 12 -26 L 22 -16 L 22 24 L -10 24 Z" fill="none" stroke="var(--cyan)" stroke-width="4"/>
    <path d="M -2 -8 H 14 M -2 2 H 14 M -2 12 H 14" stroke="var(--cyan)" stroke-width="3"/>
    <circle cx="-14" cy="12" r="12" fill="var(--cyan)"/>
    <path d="M -20 12 L -15 17 L -8 8" fill="none" stroke="#fff" stroke-width="3"/>
  </g>

  <g class="badge badge--payment" transform="translate(597 1433)">
    <circle r="82" fill="#fff" stroke="var(--blue)" stroke-width="2.5"/>
    <circle r="72" fill="var(--blue)"/>
    <circle class="icon-shadow" r="43" cx="7" cy="7"/>
    <circle class="icon-face" r="43"/>
    <rect x="-12" y="-26" width="36" height="20" rx="2" fill="none" stroke="var(--blue)" stroke-width="4" transform="rotate(-12)"/>
    <circle cx="6" cy="-14" r="5" fill="var(--blue)"/>
    <rect x="-28" y="6" width="8" height="20" fill="var(--blue)"/>
    <path d="M -18 10 L 2 10 L 8 16 L 24 8 L 26 14 L 6 26 L -18 26 Z" fill="var(--blue)"/>
  </g>

  <g class="badge badge--pilots" transform="translate(221 1252)">
    <circle r="82" fill="#fff" stroke="var(--purple)" stroke-width="2.5"/>
    <circle r="72" fill="var(--purple)"/>
    <circle class="icon-shadow" r="43" cx="7" cy="7"/>
    <circle class="icon-face" r="43"/>
    <path d="M 0 2 C -24 -12 -16 -30 0 -20 C 16 -30 24 -12 0 2 Z" fill="var(--purple)"/>
    <path d="M -4 -15 H 4 M 0 -19 V -11" stroke="#fff" stroke-width="3"/>
    <path d="M -26 -6 V 16 L -6 28 M 26 -6 V 16 L 6 28" fill="none" stroke="var(--purple)" stroke-width="5" stroke-linecap="round"/>
  </g>

  <g class="badge badge--feedback" transform="translate(128 845)">
    <circle r="82" fill="#fff" stroke="var(--pink)" stroke-width="2.5"/>
    <circle r="72" fill="var(--pink)"/>
    <circle class="icon-shadow" r="43" cx="7" cy="7"/>
    <circle class="icon-face" r="43"/>
    <path d="M -16 -28 V -18 A 8 8 0 0 0 0 -18 V -28 M -8 -10 V -4 Q -8 4 4 2 Q 12 0 12 -10" fill="none" stroke="var(--pink)" stroke-width="3.5"/>
    <circle cx="12" cy="-16" r="5" fill="none" stroke="var(--pink)" stroke-width="3"/>
    <rect x="-28" y="4" width="56" height="22" rx="3" fill="var(--pink)"/>
    <path d="M -17 9 l 2.4 5 5.3 .6 -4 3.6 1.1 5.2 -4.8 -2.7 -4.8 2.7 1.1 -5.2 -4 -3.6 5.3 -.6 Z" fill="#fff"/>
    <path d="M 0 9 l 2.4 5 5.3 .6 -4 3.6 1.1 5.2 -4.8 -2.7 -4.8 2.7 1.1 -5.2 -4 -3.6 5.3 -.6 Z" fill="#fff"/>
    <path d="M 17 9 l 2.4 5 5.3 .6 -4 3.6 1.1 5.2 -4.8 -2.7 -4.8 2.7 1.1 -5.2 -4 -3.6 5.3 -.6 Z" fill="#fff"/>
  </g>

  <g class="badge badge--publication" transform="translate(388 519)">
    <circle r="82" fill="#fff" stroke="var(--red)" stroke-width="2.5"/>
    <circle r="72" fill="var(--red)"/>
    <circle class="icon-shadow" r="43" cx="7" cy="7"/>
    <circle class="icon-face" r="43"/>
    <path d="M -8 -28 H 22 V 20" fill="none" stroke="var(--red)" stroke-width="3"/>
    <rect x="-20" y="-22" width="34" height="48" fill="var(--red)"/>
    <path d="M -14 -14 H 8 M -14 -7 H 8 M -14 0 H 8 M -14 7 H 8 M -14 14 H 8" stroke="#fff" stroke-width="2.5"/>
  </g>

  <!-- labels -->
  <g class="label label--publication">
    <text class="p-heading" x="456" y="648">Publication:</text>
    <text class="p-text" x="456" y="681">Do they have evidence</text>
    <text class="p-text" x="456" y="711">their product works?</text>
  </g>
  <g class="label label--product">
    <text class="p-heading" x="736" y="648">Product:</text>
    <text class="p-text" x="736" y="681">What is their</text>
    <text class="p-text" x="736" y="711">market solution?</text>
  </g>
  <g class="label label--property">
    <text class="p-heading" x="900" y="843">(Intellectual)</text>
    <text class="p-heading" x="900" y="876">Property:</text>
    <text class="p-text" x="900" y="909">Do they have a</text>
    <text class="p-text" x="900" y="938">patent or</text>
    <text class="p-text" x="900" y="967">trademark?</text>
  </g>
  <g class="label label--feedback">
    <text class="p-heading" x="297" y="827">Physician and</text>
    <text class="p-heading" x="297" y="859">Patient</text>
    <text class="p-heading" x="297" y="892">feedback:</text>
    <text class="p-text" x="297" y="924">Do doctors and</text>
    <text class="p-text" x="297" y="953">patients like</text>
    <text class="p-text" x="297" y="983">their product?</text>
  </g>
  <g class="label label--clearance">
    <text class="p-heading" x="830" y="1093">Product</text>
    <text class="p-heading" x="830" y="1126">Clearance:</text>
    <text class="p-text" x="830" y="1158">How will they get</text>
    <text class="p-text" x="830" y="1187">RLT approval</text>
    <text class="p-text" x="830" y="1216">and NVB</text>
    <text class="p-text" x="830" y="1245">clearance?</text>
  </g>
  <g class="label label--pilots">
    <text class="p-heading" x="362" y="1095">Pilots:</text>
    <text class="p-text" x="362" y="1131">Have they</text>
    <text class="p-text" x="362" y="1160">applied their solution</text>
    <text class="p-text" x="362" y="1189">in a</text>
    <text class="p-text" x="362" y="1218">healthcare</text>
    <text class="p-text" x="362" y="1247">setting?</text>
  </g>
  <g class="label label--payment">
    <text class="p-heading" x="594" y="1234">Payment:</text>
    <text class="p-text" x="594" y="1271">How will they</text>
    <text class="p-text" x="594" y="1300">make money?</text>
  </g>
</svg>
</body>
</html>
```